Brook Refrigeration. Refrigeration and air conditioning specialists.

We need a website to promote our business. We would a modern simple design using the colours from our logo and black. We want it to be fun but proffesional.

Target Market(s)

Commercial

Number of Pages Required

4 page

Requirements
Must have
• Home Page, About Us, Services and Contact Us.
• 24/7 365 days service available.
• Brook Refrigeration's dedicated team specialises in commercial refrigeration and air conditioning equipment.
• Based in Joondalup, we cover Perth Metro and surrounding areas.
Nice to have
• KNOWLEDGE . EXPERIENCE . PASSION in bold.
• Our experienced and highly trained technicians provide extensive knowledge and exceptional skills for your commercial refrigeration and air conditioning requirements.
• Pictures of commercial refrigeration.
Should not have
• No mention of domestic services.

```html
<!DOCTYPE html>
<html lang="en">
<head>
<meta charset="utf-8">
<title>Brook Refrigeration</title>
<link href="https://fonts.googleapis.com/css2?family=Roboto:wght@400;500;700&family=Roboto+Condensed:wght@400;700&display=swap" rel="stylesheet">
<style>
:root{
  --lime:#9fe45a;
  --lime-dark:#7fc93e;
  --purple:#3c2363;
  --purple-deep:#2f1a52;
  --ink:#333333;
  --grey:#6d6d6d;
  --line:#c9c9c9;
  --white:#ffffff;
  --footer:#2f2f2f;
}
*{margin:0;padding:0;box-sizing:border-box}
html,body{width:1200px;height:3495px;overflow:hidden}
body{position:relative;font-family:"Roboto",sans-serif;color:var(--ink);background:var(--white)}
.abs{position:absolute}
.center{text-align:center}

/* header */
.brand{left:112px;top:30px;width:170px;color:var(--lime-dark);font-family:"Roboto Condensed",sans-serif;font-weight:700;font-size:30px;line-height:32px;letter-spacing:1px}
.info{text-align:center;font-size:15px;color:var(--ink)}
.info b{display:block;font-size:24px;color:var(--purple);font-weight:700;margin-top:4px}
.info span{display:block;font-size:15px;color:var(--purple);margin-top:8px}
.social{display:flex;gap:14px;justify-content:center;margin-top:10px}
.social i{width:20px;height:20px;border-radius:50%;background:var(--purple);display:block}
.service-clock{left:950px;top:30px;width:150px;text-align:center;color:var(--purple)}
.service-clock .dot{width:40px;height:40px;border-radius:50%;background:var(--purple);margin:0 auto 6px}
.service-clock strong{font-size:27px;font-weight:700}
.service-clock small{font-size:15px;font-weight:700}

/* nav */
.nav{left:0;top:140px;width:1200px;height:35px;background:var(--purple)}
.nav a{position:absolute;top:0;height:35px;line-height:35px;color:var(--white);text-decoration:none;font-size:15px;text-align:center}
.nav a.active{background:var(--lime);color:var(--purple);font-weight:700}
.search{left:895px;top:144px;width:240px;height:27px;background:var(--white);font-size:12px;line-height:27px;padding-left:12px;color:var(--ink)}

/* hero */
.hero{left:0;top:175px;width:1200px;height:633px;background:linear-gradient(90deg,#4a4d52 0%,#7b8085 45%,#9aa0a4 70%,#6d7378 100%)}
.hero-shade{left:0;top:175px;width:760px;height:633px;background:linear-gradient(90deg,rgba(20,20,25,.55),rgba(20,20,25,0))}
.hero-rule{left:0;top:806px;width:1200px;height:4px;background:var(--lime)}
.hero-lead{left:80px;top:400px;width:656px;color:var(--white);font-size:28px}
.hero-title{left:80px;top:440px;width:656px;color:var(--white);font-family:"Roboto Condensed",sans-serif;font-weight:700;font-size:39px;line-height:43px}
.hero-tag{left:80px;top:534px;width:656px;color:var(--lime);font-weight:700;font-size:25px;letter-spacing:2px}
.btn-hero{left:322px;top:590px;width:175px;height:44px;background:var(--lime);color:var(--purple);font-family:"Roboto Condensed",sans-serif;font-size:22px;line-height:44px;text-align:center;border-radius:3px}
.dots{left:383px;top:755px;display:flex;gap:8px}
.dots i{width:9px;height:9px;border-radius:50%;border:1.5px solid var(--white);display:block}
.dots i.on{background:var(--white)}

/* section headings */
.heading{left:0;width:1200px;text-align:center;font-size:30px;font-weight:500;color:var(--purple)}
.rule{width:72px;height:2px;background:var(--purple);left:564px}

/* about */
.about-text{left:230px;width:740px;text-align:center;font-size:12.5px;line-height:22px;color:var(--grey)}
.btn-pill{height:33px;border-radius:17px;background:var(--purple);color:var(--white);font-size:12px;line-height:33px;padding-left:22px}
.btn-pill .arrow{position:absolute;right:4px;top:4px;width:25px;height:25px;border-radius:50%;background:var(--lime)}

/* services */
.services{left:0;top:1288px;width:1200px;height:1037px;background:var(--purple)}
.services .heading{color:var(--lime)}
.services-intro{left:150px;top:1415px;width:900px;text-align:center;font-size:12.5px;line-height:23px;color:#ddd5ee}
.card{width:289px;height:312px;border-radius:14px;background:linear-gradient(#ffffff 40%,#dcdcdc);overflow:hidden}
.card .band{position:absolute;left:0;top:0;width:289px;height:70px;background:var(--lime)}
.card .pic{position:absolute;left:85px;top:12px;width:118px;height:118px;border-radius:50%;border:7px solid var(--lime);background:radial-gradient(#eef0f2,#b9bec3)}
.card h3{position:absolute;left:0;top:152px;width:289px;text-align:center;font-size:18px;font-weight:500;color:var(--purple)}
.card p{position:absolute;left:30px;top:186px;width:229px;text-align:center;font-size:12px;line-height:17px;color:var(--grey)}
.card-btn{width:150px;height:33px;border-radius:17px;background:var(--lime);color:var(--white);font-size:12px;line-height:33px;padding-left:22px}
.card-btn .arrow{position:absolute;right:4px;top:4px;width:25px;height:25px;border-radius:50%;background:var(--white)}

/* contact */
.label{font-size:13px;color:var(--ink)}
.label em{color:var(--purple);font-style:normal}
.field{border:1.5px solid var(--line);background:var(--white)}
.check{width:15px;height:15px;border:1.5px solid var(--line)}

/* newsletter */
.newsletter{left:0;top:2945px;width:1200px;height:154px;background:var(--lime)}
.news-title{left:175px;top:3012px;font-size:25px;font-weight:700;color:var(--purple)}
.news-input{left:382px;top:2999px;width:506px;height:51px;background:var(--white)}
.news-btn{left:888px;top:2999px;width:128px;height:51px;background:var(--purple);color:var(--white);font-size:14px;font-weight:700;line-height:51px;text-align:center}

/* footer */
.footer{left:0;top:3099px;width:1200px;height:319px;background:var(--footer)}
.foot-brand{left:100px;top:3210px;width:160px;text-align:center;color:var(--white);font-family:"Roboto Condensed",sans-serif;font-weight:700;font-size:30px;line-height:34px}
.foot-head{font-size:17px;font-weight:700;color:var(--lime)}
.foot-text{font-size:14px;line-height:20px;color:var(--white)}
.foot-text b{color:var(--lime);font-weight:700;display:block}
.foot-links a{display:block;color:var(--white);text-decoration:none;font-size:14px;line-height:33px}
.foot-field{background:var(--white);height:37px;font-size:13px;line-height:37px;padding-left:10px;color:var(--grey)}
.foot-send{left:794px;top:3304px;width:130px;height:37px;background:var(--lime);color:var(--purple);font-size:16px;font-weight:700;line-height:37px;text-align:center}
.bottom{left:0;top:3418px;width:1200px;height:77px;background:var(--purple-deep);color:#cfc6e0;font-size:12px;line-height:77px;text-align:center}
</style>
</head>
<body>

<!-- header -->
<div class="abs brand">Brook<br>Refrigeration</div>
<div class="abs info" style="left:318px;top:58px;width:180px">Call us<b>1-888-555-0142</b></div>
<div class="abs info" style="left:480px;top:58px;width:260px">Email<span>info@brookrefrigeration.com</span></div>
<div class="abs info" style="left:720px;top:55px;width:155px">Follow us
  <div class="social"><i></i><i></i><i></i><i></i></div>
</div>
<div class="abs service-clock"><div class="dot"></div><strong>24/7</strong> <small>365 DAYS</small></div>

<!-- nav -->
<nav class="abs nav">
  <a class="active" href="#" style="left:130px;width:138px">HOME</a>
  <a href="#" style="left:290px;width:156px">ABOUT US</a>
  <a href="#" style="left:483px;width:156px">SERVICES</a>
  <a href="#" style="left:672px;width:156px">CONTACT US</a>
</nav>
<div class="abs search">Search
  <svg class="abs" style="right:8px;top:8px" width="11" height="11" viewBox="0 0 11 11"><circle cx="4.5" cy="4.5" r="3.5" fill="none" stroke="#555" stroke-width="1.4"/><line x1="7" y1="7" x2="10.5" y2="10.5" stroke="#555" stroke-width="1.6"/></svg>
</div>

<!-- hero -->
<div class="abs hero" role="img" aria-label="Photo of a smiling refrigeration technician holding a clipboard in a commercial kitchen"></div>
<div class="abs hero-shade"></div>
<div class="abs hero-lead center">Our dedicated team specialises in</div>
<div class="abs hero-title center">COMMERCIAL REFRIGERATION &amp;<br>AIR CONDITIONING EQUIPMENT.</div>
<div class="abs hero-tag center">KNOWLEDGE · EXPERIENCE · PASSION</div>
<div class="abs btn-hero">KNOW MORE</div>
<div class="abs dots"><i class="on"></i><i></i><i></i></div>
<div class="abs hero-rule"></div>

<!-- about -->
<h2 class="abs heading" style="top:893px">About us</h2>
<div class="abs rule" style="top:940px"></div>
<p class="abs about-text" style="top:965px">Brook Refrigeration's dedicated team specialises in commercial refrigeration and air conditioning equipment.<br>Based in Joondalup, we cover Perth Metro and surrounding areas.</p>
<p class="abs about-text" style="top:1033px;left:200px;width:800px">ILorem ipsum dolor sit amet, consectetur adipiscing elit. Morbi auctor ullamcorper congue. Phasellus quis lacus quis ante ornare tincidunt lobortis quis enim. Nam lacinia ex ac quam sollicitudin placerat. Nullam eu laoreet diam. Vivamus sed mattis erat. Cras fringilla maximus magna, eleifend pellentesque tellus volutpat eu. Sed sed ornare dolor, quis tempor justo. Curabitur at turpis justo. Curabitur sem sapien, vulputate sed semper efficitur.</p>
<div class="abs btn-pill" style="left:531px;top:1137px;width:138px">READ MORE<span class="arrow"></span></div>

<!-- services -->
<section class="abs services"></section>
<h2 class="abs heading" style="top:1336px;color:var(--lime)">Our Services</h2>
<div class="abs rule" style="top:1383px;background:var(--lime)"></div>
<p class="abs services-intro">Whether you wish to cool, store or display food and drink, we have a wide range of commercial refrigerator services catering to various small and large scale industries.<br>We specialize in wide range of commercial refrigeration operations and maintenance services to ensure efficient functioning of the systems.</p>

<svg class="abs" style="left:56px;top:1826px" width="26" height="52" viewBox="0 0 26 52"><polyline points="24,2 2,26 24,50" fill="none" stroke="#7d6a9c" stroke-width="2"/></svg>
<svg class="abs" style="left:1118px;top:1826px" width="26" height="52" viewBox="0 0 26 52"><polyline points="2,2 24,26 2,50" fill="none" stroke="#7d6a9c" stroke-width="2"/></svg>

<div class="abs card" style="left:133px;top:1496px"><div class="band"></div><div class="pic" role="img" aria-label="Commercial chest freezer"></div><h3>Commercial Freezer</h3><p>Lorem ipsum dolor sit amet, consectetur adipiscing elit. Morbi auctor ullamcorper congue. Phasellus quis lacus quis ante ornare tincidunt lobortis quisenim.</p></div>
<div class="abs card" style="left:457px;top:1496px"><div class="band"></div><div class="pic" role="img" aria-label="Walk in cooler room"></div><h3>Walk In Cooler</h3><p>Lorem ipsum dolor sit amet, consectetur adipiscing elit. Morbi auctor ullamcorper congue. Phasellus quis lacus quis ante ornare tincidunt lobortis quisenim.</p></div>
<div class="abs card" style="left:781px;top:1496px"><div class="band"></div><div class="pic" role="img" aria-label="Stainless steel kitchen refrigerator"></div><h3>Kitchen Refrigeration</h3><p>Lorem ipsum dolor sit amet, consectetur adipiscing elit. Morbi auctor ullamcorper congue. Phasellus quis lacus quis ante ornare tincidunt lobortis quisenim.</p></div>
<div class="abs card" style="left:133px;top:1906px"><div class="band"></div><div class="pic" role="img" aria-label="Glass door drinks merchandiser"></div><h3>Glass Door Merchandiser</h3><p>Lorem ipsum dolor sit amet, consectetur adipiscing elit. Morbi auctor ullamcorper congue. Phasellus quis lacus quis ante ornare tincidunt lobortis quisenim.</p></div>
<div class="abs card" style="left:457px;top:1906px"><div class="band"></div><div class="pic" role="img" aria-label="Curved glass bakery display case"></div><h3>Bakery Display Case</h3><p>Lorem ipsum dolor sit amet, consectetur adipiscing elit. Morbi auctor ullamcorper congue. Phasellus quis lacus quis ante ornare tincidunt lobortis quisenim.</p></div>
<div class="abs card" style="left:781px;top:1906px"><div class="band"></div><div class="pic" role="img" aria-label="Stainless steel ice machine"></div><h3>Ice machines</h3><p>Lorem ipsum dolor sit amet, consectetur adipiscing elit. Morbi auctor ullamcorper congue. Phasellus quis lacus quis ante ornare tincidunt lobortis quisenim.</p></div>

<div class="abs card-btn" style="left:203px;top:1792px">READ MORE<span class="arrow"></span></div>
<div class="abs card-btn" style="left:527px;top:1792px">READ MORE<span class="arrow"></span></div>
<div class="abs card-btn" style="left:851px;top:1792px">READ MORE<span class="arrow"></span></div>
<div class="abs card-btn" style="left:203px;top:2202px">READ MORE<span class="arrow"></span></div>
<div class="abs card-btn" style="left:527px;top:2202px">READ MORE<span class="arrow"></span></div>
<div class="abs card-btn" style="left:851px;top:2202px">READ MORE<span class="arrow"></span></div>

<!-- contact -->
<h2 class="abs heading" style="top:2412px;font-size:34px">Contact Us</h2>
<div class="abs label" style="left:151px;top:2520px">Name <em>*</em></div>
<div class="abs field" style="left:151px;top:2544px;width:397px;height:40px"></div>
<div class="abs label" style="left:151px;top:2605px">Email <em>*</em></div>
<div class="abs field" style="left:151px;top:2630px;width:397px;height:38px"></div>
<div class="abs label" style="left:151px;top:2691px">Phone</div>
<div class="abs field" style="left:151px;top:2716px;width:397px;height:38px"></div>
<div class="abs label" style="left:673px;top:2520px">Description</div>
<div class="abs field" style="left:673px;top:2544px;width:397px;height:133px"></div>
<div class="abs label" style="left:673px;top:2689px;font-size:12px;color:var(--grey)"><em>*</em> Required</div>
<div class="abs check" style="left:676px;top:2727px"></div>
<div class="abs label" style="left:702px;top:2727px;color:var(--grey)">I have read the Disclaimer and Privacy Policy</div>
<div class="abs btn-pill" style="left:531px;top:2819px;width:138px;padding-left:30px">SUBMIT<span class="arrow"></span></div>

<!-- newsletter -->
<div class="abs newsletter"></div>
<div class="abs news-title">NEWSLETTER</div>
<div class="abs news-input"></div>
<div class="abs news-btn">SUBSCRIBE</div>

<!-- footer -->
<footer class="abs footer"></footer>
<div class="abs foot-brand">Brook<br>Refrigeration</div>

<div class="abs foot-head" style="left:359px;top:3163px">CONTACT US</div>
<svg class="abs" style="left:352px;top:3205px" width="22" height="30" viewBox="0 0 22 30"><path d="M11 1C5.5 1 1 5.3 1 10.8 1 18 11 29 11 29s10-11 10-18.2C21 5.3 16.5 1 11 1z" fill="var(--lime)"/><circle cx="11" cy="10.5" r="4" fill="var(--footer)"/></svg>
<div class="abs foot-text" style="left:392px;top:3205px"><b>ADDRESS</b>18 Lakeside Drive<br>Joondalup WA 6027</div>
<svg class="abs" style="left:352px;top:3288px" width="24" height="24" viewBox="0 0 24 24"><path d="M6.6 10.8a15.1 15.1 0 0 0 6.6 6.6l2.2-2.2c.3-.3.7-.4 1-.2 1.1.4 2.3.6 3.6.6.6 0 1 .4 1 1V20c0 .6-.4 1-1 1C10.6 21 3 13.4 3 4c0-.6.4-1 1-1h3.5c.6 0 1 .4 1 1 0 1.3.2 2.5.6 3.6.1.3 0 .7-.2 1z" fill="var(--lime)"/></svg>
<div class="abs foot-text" style="left:392px;top:3290px"><b style="color:var(--white)">PHONE NUMBER</b>1-888-555-0142</div>

<div class="abs foot-head" style="left:624px;top:3163px">ABOUT</div>
<div class="abs foot-links" style="left:628px;top:3205px"><a href="#">Home</a><a href="#">About Us</a><a href="#">Services</a><a href="#">Contact us</a></div>

<div class="abs foot-head" style="left:790px;top:3163px">GET IN TOUCH</div>
<div class="abs foot-field" style="left:794px;top:3206px;width:152px">Name</div>
<div class="abs foot-field" style="left:951px;top:3206px;width:152px">Phone</div>
<div class="abs foot-field" style="left:794px;top:3248px;width:309px">Email address</div>
<div class="abs foot-send">SEND</div>

<div class="abs bottom">© 2018 brookrefrigeration All Right Reserved</div>

</body>
</html>
```